Business card design for a dynamic IT consulting company

We need a business card design for a young firm, specialized in the Telecommunications/Consulting industry. The name of the company is Quindor and Partners Business Consulting Ltd. (Short name: Quindor and Partnes)
Quindor = solve read reverse, so we aim to be uncomplicated and solution-oriented. The small pipe in our logo is also related to the word solve. So we need a new business card design, which is simple, eye catching and something non traditional (I would probably prefer a square shaped design rather than a rectangle, but open for suggestions). Attached our logo.

Target Market(s)

Usually our customers are Tier1 Telecoms providers (Q-Netra, Palorix, etc) and their executives.

Industry/Entity Type

Business

Contact Information for Business Card

Name: Bence Tolnavari
Email: b.tolnavari@quindor.hu
Web: www.quindor.hu
Mobile: +36 30 518 2769
Title: Managing Director

Optional:
Company name: Quindor and Partners Ltd.
Address: 1087 Budapest, Tolvenka str. 28/C, Hungary

Font styles to use
Other font styles liked:
• helveticaneue_medium, Prime Regular are used now.

Colors

Designer to choose colors to be used in the design.

Requirements
Must have
• I would like to have a 2 sided design.
Nice to have
• I thought if we make the logo a bit bigger (without the company name), that could go to the back with the company name below. I though, if the pipe in the logo is somehow touchable on the business card, would be nice and unique.

```html
<!DOCTYPE html>
<html lang="en">
<head>
<meta charset="utf-8">
<title>Quindor &amp; Partners — Business Card</title>
<link rel="stylesheet" href="https://fonts.googleapis.com/css2?family=Work+Sans:wght@400;500&family=Quicksand:wght@600;700&display=swap">
<style>
  :root {
    --brand-blue: #1b9ad6;
    --ink-grey: #5a5a5a;
    --band-grey: #5f5f60;
    --paper: #ffffff;
    --backdrop: #2a2a2a;
  }
  * { margin: 0; padding: 0; box-sizing: border-box; }
  html, body { width: 1200px; height: 930px; overflow: hidden; background: var(--backdrop); }
  .canvas { position: relative; width: 1200px; height: 930px; font-family: "Work Sans", sans-serif; }

  .card { position: absolute; left: 277px; width: 646px; height: 370px; overflow: hidden; }
  .card--front { top: 75px; background: var(--paper); }
  .card--back { top: 486px; background: var(--brand-blue); }

  .brand { position: absolute; display: flex; align-items: center; font-family: "Quicksand", sans-serif; font-weight: 600; white-space: nowrap; }
  .brand__square { display: block; background: currentColor; }
  .brand--front { left: 31px; top: 42px; color: var(--ink-grey); font-size: 30px; gap: 12px; }
  .brand--front .brand__square { width: 12px; height: 12px; color: var(--brand-blue); }
  .brand--back { left: 0; right: 0; top: 155px; justify-content: center; color: #fff; font-size: 46px; gap: 20px; }
  .brand--back .brand__square { width: 22px; height: 22px; }

  .holder { position: absolute; right: 31px; top: 204px; text-align: right; }
  .holder__name { font-family: "Quicksand", sans-serif; font-weight: 700; font-size: 24px; color: var(--brand-blue); line-height: 1.1; }
  .holder__title { margin-top: 4px; font-size: 15.5px; color: var(--ink-grey); }
  .divider { position: absolute; left: 32px; top: 244px; width: 435px; height: 1px; background: var(--brand-blue); }

  .contacts { position: absolute; left: 31px; top: 266px; list-style: none; font-size: 15.5px; color: var(--ink-grey); }
  .contacts li { display: flex; align-items: center; height: 20.5px; }
  .contacts svg { width: 11px; height: 11px; margin-right: 11px; flex: none; }
  .address { position: absolute; right: 31px; top: 286px; text-align: right; font-size: 15.5px; line-height: 20.5px; color: var(--ink-grey); font-style: normal; }

  .footer-band { position: absolute; left: 0; bottom: 0; width: 646px; height: 30px; }
</style>
</head>
<body>
<main class="canvas">
  <section class="card card--front" aria-label="Card front">
    <div class="brand brand--front"><span class="brand__square"></span>Quindor &amp; Partners</div>

    <div class="holder">
      <p class="holder__name">Bence Tolnavari</p>
      <p class="holder__title">Managing Director</p>
    </div>
    <div class="divider"></div>

    <ul class="contacts">
      <li>
        <svg viewBox="0 0 12 12" aria-hidden="true"><path d="M3 1.2 4.6 3.6 3.6 4.6c.6 1.5 1.9 2.9 3.6 3.7l1-1L10.8 9 9.6 10.6C5.4 10 2 6.6 1.5 2.4Z" fill="var(--brand-blue)"/></svg>
        +36 30 518 2769
      </li>
      <li>
        <svg viewBox="0 0 12 12" aria-hidden="true"><rect x="1" y="2.5" width="10" height="7" rx="1" fill="none" stroke="var(--brand-blue)" stroke-width="1.2"/><path d="M1.5 3 6 6.5 10.5 3" fill="none" stroke="var(--brand-blue)" stroke-width="1.2"/></svg>
        b.tolnavari@quindor.hu
      </li>
      <li>
        <svg viewBox="0 0 12 12" aria-hidden="true"><g fill="none" stroke="var(--brand-blue)" stroke-width="1"><circle cx="6" cy="6" r="4.8"/><ellipse cx="6" cy="6" rx="2" ry="4.8"/><path d="M1.2 6h9.6M2 3.5h8M2 8.5h8"/></g></svg>
        www.quindor.hu
      </li>
    </ul>

    <address class="address">1087 Budapest,<br>Tolvenka str. 28/C, Hungary</address>

    <svg class="footer-band" viewBox="0 0 646 30" preserveAspectRatio="none" aria-hidden="true">
      <path d="M0 16H372C384 16 400 10 414 5 C424 1.5 432 0 444 0H646V30H0Z" fill="var(--brand-blue)"/>
      <path d="M0 8H374C382 8 388 6.5 394 5H410C400 9 390 12 378 12H0Z" fill="var(--band-grey)"/>
    </svg>
  </section>

  <section class="card card--back" aria-label="Card back">
    <div class="brand brand--back"><span class="brand__square"></span>Quindor &amp; Partners</div>
  </section>
</main>
</body>
</html>
```